Automotive component supplier needs a business card design

We need a business card design for our company called Velran Global Components Ltd based in the UK. We are a supplier of interior and exterior components to premium car manufacturers such as Corvel Ashby, Hadley Fenn, Marquist and Tavarelli. We would like to see a modern business card design that uses the colour blue.

Target Market(s)

Premium automotive car manufacturers.

Industry/Entity Type

Automotive

Contact Information for Business Card

Company Name : Velran Global Components Limited
Address: 17 Marlow Yard, Upper Heath, Warwick, CV31 8QL, United Kingdom
Web Address : www.velrancomponents-example.co.uk

Font styles to use
Other font styles liked:
• Helvetica

Colors
3176b5
0255a3
85acd3
cfdeed
cee9f5
85cae6
34a6d7
0692cd
9bcb3c

Requirements
Must have
• Clear company logo and a mixture of blue colours.
Nice to have
• A high quality modern image.
Should not have
• Multiple colours.

```html
<!DOCTYPE html>
<html lang="en">
<head>
<meta charset="utf-8">
<title>Velran Global Components – Business Card</title>
<link rel="stylesheet" href="https://fonts.googleapis.com/css2?family=Open+Sans:wght@400;600;700&display=swap">
<style>
  :root {
    --brand-blue: #0692cd;
    --deep-blue: #0255a3;
    --leaf-green: #9bcb3c;
    --ink: #1e1e1e;
    --paper: #ffffff;
    --backdrop: #e9edf1;
  }
  * { box-sizing: border-box; margin: 0; padding: 0; }
  html, body {
    width: 1200px; height: 900px; overflow: hidden;
    background: var(--backdrop);
    font-family: "Open Sans", Arial, sans-serif;
  }
  .sheet {
    width: 1200px; height: 900px;
    display: flex; align-items: center; justify-content: center; gap: 40px;
  }
  .card {
    position: relative;
    width: 540px; height: 309px;
    overflow: hidden;
    box-shadow: 0 6px 18px rgba(0,0,0,0.12);
  }
  .card--front { background: var(--paper); }
  .card--back {
    background: var(--brand-blue);
    display: flex; align-items: center; justify-content: center;
  }
  .card__bands { position: absolute; inset: 0; }

  .wordmark {
    font-weight: 700;
    color: var(--brand-blue);
    text-transform: uppercase;
    line-height: 1;
    text-align: left;
  }
  .wordmark__name { display: block; font-size: 60px; letter-spacing: 4px; }
  .wordmark__tagline { display: block; font-size: 15px; letter-spacing: 3.2px; margin-top: 6px; }
  .card--back .wordmark { color: var(--paper); }
  .card--back .wordmark__name { font-size: 72px; letter-spacing: 5px; }
  .card--back .wordmark__tagline { font-size: 18px; letter-spacing: 3.8px; }

  .card--front .wordmark { position: absolute; left: 262px; top: 112px; }
  .card--front .wordmark__name { font-size: 48px; letter-spacing: 3px; }
  .card--front .wordmark__tagline { font-size: 12px; letter-spacing: 2.2px; }

  .holder { position: absolute; left: 16px; top: 16px; display: flex; gap: 8px; }
  .holder__name { font-size: 15px; font-weight: 700; color: var(--brand-blue); line-height: 1.1; }
  .holder__role { font-size: 10px; color: var(--ink); }

  .contact { position: absolute; left: 26px; top: 112px; list-style: none; }
  .contact__item {
    display: flex; align-items: center; gap: 8px;
    font-size: 11.5px; color: var(--ink); line-height: 16px;
  }
  .contact__item svg { width: 9px; height: 9px; fill: var(--brand-blue); flex: none; }
  .address {
    position: absolute; left: 14px; top: 182px;
    font-style: normal; font-size: 11.5px; line-height: 16px; color: var(--ink);
  }
</style>
</head>
<body>
<main class="sheet">
  <section class="card card--front" aria-label="Card front">
    <svg class="card__bands" viewBox="0 0 540 309" aria-hidden="true">
      <polygon points="0,236 190,236 176,252 0,252" fill="var(--leaf-green)"/>
      <polygon points="196,252 540,252 540,309 150,309" fill="var(--brand-blue)"/>
    </svg>

    <div class="holder">
      <svg width="26" height="20" viewBox="0 0 26 20" aria-hidden="true">
        <rect x="0" y="0" width="9" height="9" fill="var(--leaf-green)"/>
        <polygon points="10,20 20,0 26,0 26,20" fill="var(--brand-blue)"/>
      </svg>
      <div>
        <p class="holder__name">Elliot Marsh</p>
        <p class="holder__role">Director</p>
      </div>
    </div>

    <ul class="contact">
      <li class="contact__item"><svg viewBox="0 0 10 10"><path d="M2 0l2 2-1 1.5c.8 1.5 2 2.7 3.5 3.5L8 6l2 2-1.5 2C4 10 0 6 0 1.5z"/></svg>01926 555 0142</li>
      <li class="contact__item"><svg viewBox="0 0 10 10"><rect x="2" y="0" width="6" height="10" rx="1"/></svg>07700 900 318</li>
      <li class="contact__item"><svg viewBox="0 0 10 10"><path d="M0 2h10v6H0z M0 2l5 3 5-3" /></svg>info@velrancomponents-example.co.uk</li>
      <li class="contact__item"><svg viewBox="0 0 10 10"><circle cx="5" cy="5" r="5"/></svg>www.velrancomponents-example.co.uk</li>
    </ul>
    <address class="address">17 Marlow Yard, Upper Heath,<br>Warwick, CV31 8QL, United Kingdom</address>

    <p class="wordmark">
      <span class="wordmark__name">Velran</span>
      <span class="wordmark__tagline">Global Components</span>
    </p>
  </section>

  <section class="card card--back" aria-label="Card back">
    <p class="wordmark">
      <span class="wordmark__name">Velran</span>
      <span class="wordmark__tagline">Global Components</span>
    </p>
  </section>
</main>
</body>
</html>
```